Construction Company

Design a clutter free business card, it can be double-sided utilizing the logo for VKM Ltd simple with all relevant contact information.

Please also a letterhead design to function for the purposes of invoicing, all mail requirements, with header to be distinctive while the footer ties page together and incorporates all necessary information.

For now, please use generic / dummy text and when a winner is selected, I will disclose the contact information.

Hi Designers! Please read the updated brief which includes the design of a business card and letterhead. Thank you!

```html
<!DOCTYPE html>
<html lang="en">
<head>
<meta charset="utf-8">
<title>VKM Ltd — Letterhead</title>
<link href="https://fonts.googleapis.com/css2?family=Montserrat:wght@400;500;700&family=Roboto:wght@400&display=swap" rel="stylesheet">
<style>
  :root {
    --navy: #0c2f8c;
    --gold: #b08d1f;
    --ink: #2b2b2b;
    --muted: #8c8c8c;
    --paper: #ffffff;
    --backdrop: #e9e9ea;
  }
  * { margin: 0; padding: 0; box-sizing: border-box; }
  html, body {
    width: 1110px; height: 1200px; overflow: hidden;
    background: var(--backdrop);
    font-family: "Montserrat", Arial, sans-serif;
  }
  .letterhead {
    position: absolute; left: 174px; top: 50px;
    width: 772px; height: 1080px;
    background: var(--paper);
    overflow: hidden;
  }
  .brand {
    position: absolute; left: 44px; top: 66px;
    display: flex; align-items: center; gap: 10px;
    color: var(--navy); font-weight: 700; font-size: 46px; letter-spacing: 1px; line-height: 1;
  }
  .brand-dot { width: 14px; height: 14px; border-radius: 50%; background: var(--gold); }
  .header-rule {
    position: absolute; left: 44px; top: 129px; width: 684px; height: 2px; background: var(--navy);
  }
  .contact {
    position: absolute; left: 579px; top: 29px;
    color: var(--navy); font-family: "Roboto", Arial, sans-serif;
    font-size: 13px; line-height: 16px; list-style: none;
  }
  .contact li { display: flex; align-items: center; gap: 7px; margin-top: 3px; white-space: nowrap; }
  .contact li.plain { margin-top: 0; }
  .contact li.plain + li:not(.plain) { margin-top: 7px; }
  .contact svg { width: 11px; height: 11px; flex: none; }
  .recipient { position: absolute; left: 79px; top: 240px; }
  .recipient .to { font-size: 14px; letter-spacing: 2px; color: var(--ink); }
  .recipient .name { font-size: 13px; color: var(--navy); margin-top: 7px; font-weight: 500; }
  .recipient .lines { font-size: 10.5px; color: var(--muted); line-height: 17px; margin-top: 3px; }
  .date { position: absolute; right: 78px; top: 238px; font-size: 10.5px; color: var(--ink); }
  .body-copy {
    position: absolute; left: 79px; top: 385px; width: 617px;
    font-size: 10.5px; line-height: 13.7px; color: var(--muted); text-align: justify;
  }
  .body-copy p { margin-bottom: 13px; }
  .signature {
    position: absolute; left: 79px; top: 766px; width: 132px; height: 25px;
    background: linear-gradient(90deg, #ececec, #f6f6f6);
  }
  .signatory { position: absolute; left: 79px; top: 803px; }
  .signatory .name { font-size: 13px; color: var(--ink); }
  .signatory .role { font-size: 9.5px; color: var(--muted); margin-top: 2px; }
  .footer-accent { position: absolute; left: 0; bottom: 44px; width: 100%; height: 6px; background: var(--gold); }
  .footer-band { position: absolute; left: 0; bottom: 0; width: 100%; height: 40px; background: var(--navy); }
</style>
</head>
<body>
  <main class="letterhead">
    <div class="brand"><span class="brand-name">VKM LTD</span><span class="brand-dot"></span></div>
    <div class="header-rule"></div>

    <ul class="contact">
      <li class="plain">Your address</li>
      <li class="plain">city, state, ZIP 0000</li>
      <li>
        <svg viewBox="0 0 12 12"><path d="M2.5 1 L4.5 1 L5.3 3.5 L4 4.5 C4.7 6 6 7.3 7.5 8 L8.5 6.7 L11 7.5 L11 9.5 C11 10.3 10.3 11 9.5 11 C5 11 1 7 1 2.5 C1 1.7 1.7 1 2.5 1 Z" fill="var(--gold)"/></svg>
        123-456-2100
      </li>
      <li>
        <svg viewBox="0 0 12 12"><rect x="1" y="2.5" width="10" height="7" fill="none" stroke="var(--gold)" stroke-width="1.2"/><path d="M1 2.5 L6 6.5 L11 2.5" fill="none" stroke="var(--gold)" stroke-width="1.2"/></svg>
        youremail@mailbox.com
      </li>
      <li>
        <svg viewBox="0 0 12 12"><circle cx="6" cy="6" r="5" fill="none" stroke="var(--gold)" stroke-width="1.1"/><ellipse cx="6" cy="6" rx="2.2" ry="5" fill="none" stroke="var(--gold)" stroke-width="1"/><path d="M1 6 H11" stroke="var(--gold)" stroke-width="1"/></svg>
        www.yourwebsite.com
      </li>
    </ul>

    <section class="recipient">
      <div class="to">TO</div>
      <div class="name">Daniel Whitford</div>
      <div class="lines">
        Human Resources<br>
        Northline Group<br>
        48-B Harbor Street, Westfield<br>
        WF21 USA
      </div>
    </section>
    <div class="date">Friday, 01/01/2018</div>

    <section class="body-copy">
      <p>Lorem ipsum dolor sit amet, consectetuer adipiscing elit, sed diam nonummy nibh euismod tincidunt ut laoreet dolore magna aliquam erat volutpat. Ut wisi enim ad minim veniam, quis nostrud exerci tationmcorper suscipit lobortis nisl ut aliquip ex ea commodo consequat. Duis autem vel eum iriure dolor in hendrerit in vulputate velit esse molestie consequat, vel illum dolore eu feugiat nulla facilisis at vero eros et accumsan et iusto odio dignissim qui blandit praesent luptatum zzril delenit augue duis dolore te feugait nulla facilisi.</p>
      <p>Nam liber tempor cum soluta nobis eleifend option congue nihil imprdiet doming id quod mazim placerat facer possim assum. Typi non habent claritatem insitam;</p>
      <p>Est usus legentis in iis qui facit eorum claritatem.</p>
      <p>Investigationes demonstraverunt lectores legere me lius quod ii legunt saepius. Claritas est etiam processus dynamicus, qui sequitur mutationem consuetudium lectorum. Mirum est notare quam littera gothica, quam nunc putamus parum claram, anteposuerit litterarum formas humanitatis per seacula quarta decima et quinta decima. Eodem modo typi, qui nunc nobis videntur parum clari, fiant sollemnes in futurum.</p>
      <p>consectetuer adipiscing elit, sed diam nonummy nibh euismod tincidunt ut laoreet dolore magna aliquam erat volutpat. Ut wisi enim ad minim veniam, quis nostrud exerci tation ullamcorper suscipit lobortis nisl ut aliquip ex ea commodo consequat. Duis autem vel eum iriure dolor in hendrerit in vulputate velit esse molestie consequat, vel illum dolore eu feugiat nulla facilisis at vero eros et accumsan et iusto odio dignissim qui blandit praesent luptatum zzril delenit augue duis dolore te feugait nulla facilisi.</p>
      <p>Nam liber tempor cum soluta nobis eleifend option congue nihil imperdiet .</p>
    </section>

    <div class="signature" role="img" aria-label="Handwritten signature of the managing director"></div>
    <section class="signatory">
      <div class="name">Oliver Bennett</div>
      <div class="role">Managing Director</div>
    </section>

    <div class="footer-accent"></div>
    <div class="footer-band"></div>
  </main>
</body>
</html>
```